Simple and Clean business card design

We would like the design to be simple clean and to incorporate our colors.

We are open to your design and talent, we have the dots in our logo as we think of it as data points and we connect data points for people.

We are open to see the great creative and clean design you bring to the table

Contact Information for Business Card

please include: name, position, email, phone and website

Font styles to use
Sans Serif

Requirements
Must have
• my colors incorporated, simplicity
Nice to have
• lots of white space, simplicity
Should not have
• complexicity/ complex art

```html
<!DOCTYPE html>
<html lang="en">
<head>
<meta charset="utf-8">
<title>Nectra Business Card</title>
<link href="https://fonts.googleapis.com/css2?family=Montserrat:wght@400;600;700&display=swap" rel="stylesheet">
<style>
  :root {
    --backdrop: #e4e4e4;
    --paper: #f7f7f7;
    --ink: #111111;
    --muted: #444444;
    --brand-blue: #2f63d8;
    --brand-blue-light: #5a8ae8;
    --brand-green: #2e8b45;
    --brand-yellow: #f0b400;
    --brand-red: #dc3a2a;
    --soft-grey: #ebebeb;
  }
  * { margin: 0; padding: 0; box-sizing: border-box; }
  html, body { width: 1200px; height: 1200px; overflow: hidden; }
  body {
    background: var(--backdrop);
    font-family: "Montserrat", sans-serif;
    position: relative;
  }
  .card {
    position: absolute;
    left: 262px;
    width: 686px;
    height: 392px;
    border-radius: 20px;
    overflow: hidden;
  }
  .card-front { top: 165px; background: var(--paper); }
  .card-back {
    top: 652px;
    background: linear-gradient(200deg, var(--brand-blue-light) 0%, var(--brand-blue) 45%, #2a5bd4 100%);
  }

  .deco { position: absolute; border-radius: 50%; }
  .dot-a { left: 318px; top: 41px; width: 63px; height: 63px; background: var(--soft-grey); }
  .dot-b { left: 435px; top: 9px; width: 83px; height: 83px; background: var(--soft-grey); }
  .dot-c { left: 548px; top: 49px; width: 124px; height: 124px; background: var(--soft-grey); }
  .ring-front {
    left: 527px; top: 217px; width: 166px; height: 166px;
    border: 27px solid var(--soft-grey);
  }

  .brand-name {
    position: absolute;
    left: 50px;
    top: 78px;
    font-weight: 600;
    font-size: 60px;
    line-height: 1;
    color: var(--ink);
    letter-spacing: 0.5px;
  }

  .contact-list {
    position: absolute;
    left: 54px;
    top: 279px;
    list-style: none;
    font-size: 16px;
    color: var(--muted);
  }
  .contact-list li { display: flex; align-items: center; gap: 8px; height: 20px; }
  .contact-list svg { width: 15px; height: 15px; flex: none; }

  .person {
    position: absolute;
    right: 62px;
    top: 286px;
    text-align: right;
  }
  .person-name { font-weight: 700; font-size: 22px; color: var(--ink); letter-spacing: 0.3px; }
  .person-role { font-size: 16px; color: var(--brand-blue-light); margin-top: 2px; }

  .edge-band {
    position: absolute;
    left: 0; bottom: 0;
    width: 100%; height: 11px;
    background: var(--ink);
  }
  .edge-band-accent {
    position: absolute;
    left: 52px; top: 0;
    width: 180px; height: 100%;
    background: var(--brand-blue);
    border-left: 3px solid #fff;
    border-right: 3px solid #fff;
  }

  .ring-back {
    left: -15px; top: 278px; width: 225px; height: 225px;
    border: 30px solid #ffffff;
  }
  .web-line {
    position: absolute;
    left: 286px;
    top: 250px;
    display: flex;
    align-items: baseline;
    color: #ffffff;
  }
  .web-line .affix { font-size: 22px; font-weight: 400; }
  .web-line .web-brand { font-size: 60px; font-weight: 600; color: var(--ink); line-height: 1; }
</style>
</head>
<body>

<section class="card card-front" aria-label="Card front">
  <div class="deco dot-a"></div>
  <div class="deco dot-b"></div>
  <div class="deco dot-c"></div>
  <div class="deco ring-front"></div>

  <div class="brand-name">Nectra</div>

  <ul class="contact-list">
    <li>
      <svg viewBox="0 0 16 16"><circle cx="8" cy="8" r="8" fill="var(--brand-green)"/><path d="M5.2 4.2l1.4 1.6-.8 1c.5 1 1.3 1.8 2.3 2.3l1-.8 1.6 1.4-.9 1.3C7.3 10.8 5 8.5 4.4 5.1z" fill="#fff"/></svg>
      555-014-2273
    </li>
    <li>
      <svg viewBox="0 0 16 16"><circle cx="8" cy="8" r="8" fill="var(--brand-yellow)"/><rect x="4" y="5" width="8" height="6" rx="1" fill="#fff"/><path d="M4.5 5.5L8 8.3l3.5-2.8" stroke="var(--brand-yellow)" stroke-width="1" fill="none"/></svg>
      info@nectra.com
    </li>
    <li>
      <svg viewBox="0 0 16 16"><circle cx="8" cy="8" r="8" fill="var(--brand-red)"/><circle cx="8" cy="8" r="3.8" fill="none" stroke="#fff" stroke-width="1.2"/><path d="M4.2 8h7.6M8 4.2c-1.5 2.2-1.5 5.4 0 7.6M8 4.2c1.5 2.2 1.5 5.4 0 7.6" stroke="#fff" stroke-width="0.9" fill="none"/></svg>
      nectra.com
    </li>
  </ul>

  <div class="person">
    <div class="person-name">DANIEL BROOKS</div>
    <div class="person-role">President</div>
  </div>

  <div class="edge-band"><div class="edge-band-accent"></div></div>
</section>

<section class="card card-back" aria-label="Card back">
  <div class="deco ring-back"></div>
  <div class="web-line">
    <span class="affix">www.</span><span class="web-brand">Nectra</span><span class="affix">.com</span>
  </div>
</section>

</body>
</html>
```